Boutique Store Selling Antiques and Unique Finds

I need a Web Page designed for my Store Called "Willow Lane". I would like a very classic, muted design that looks European when pulled up. I will be selling Antiques from all over the world and Unique finds that have reproduced. I will also be selling high-end purses and jewelry with unique, reasonable products for the every-day buyer as well.

Target Market(s)

25-70 year old men and women;)

Coding

Coded - Design and coding required

Number of Pages Required

1 page

Colors

Designer to choose only greyscale colors for use in the design.

Requirements
Must have
• I want it

```html
<!DOCTYPE html>
<html lang="en">
<head>
<meta charset="utf-8">
<title>Willow Lane — Antiques &amp; Unique Finds</title>
<link href="https://fonts.googleapis.com/css2?family=Cinzel:wght@400;600&family=Open+Sans:wght@400;600;700&display=swap" rel="stylesheet">
<style>
:root{
  --mint:#e3f0ee;
  --line:#cfdedc;
  --ink:#1b1f1e;
  --slate:#34423f;
  --footer:#36433f;
  --muted:#5c6664;
  --white:#ffffff;
  --card-border:#d5dcdb;
}
*{box-sizing:border-box;margin:0;padding:0}
html,body{width:1200px;height:3183px;overflow:hidden;background:var(--mint)}
body{font-family:"Open Sans",Arial,sans-serif;color:var(--ink);position:relative}
.page{position:relative;width:1200px;height:3183px;overflow:hidden}
.abs{position:absolute}

/* header */
.search{left:144px;top:28px;width:220px;height:36px;background:var(--white);border:1px solid var(--line);font-size:12px;color:#666;padding:10px 8px}
.search svg{position:absolute;right:14px;top:11px}
.brand{font-family:"Cinzel",serif;font-weight:600;letter-spacing:4px;color:var(--ink)}
.header-brand{left:0;width:1200px;top:38px;text-align:center;font-size:30px}
.account{left:864px;top:36px;font-size:14px;color:var(--muted)}
.cart{left:997px;top:36px;font-size:14px;color:var(--muted)}
.cart svg{vertical-align:-2px;margin-right:4px}
.header-rule{left:0;top:109px;width:1200px;height:1px;background:var(--line)}
.nav{left:201px;top:144px;display:flex;gap:26px;font-size:13px;color:var(--ink)}

/* hero */
.hero{left:0;top:183px;width:1200px;height:542px;background:radial-gradient(ellipse at 50% 100%,#3d3d3d 0%,#6a6a6a 45%,#8c8c8c 100%)}
.hero-title{left:144px;top:258px;font-size:56px;color:var(--white);letter-spacing:6px}
.hero-sub{left:144px;top:336px;font-size:24px;font-weight:700;color:var(--white)}
.btn{left:146px;top:409px;width:170px;height:46px;background:var(--slate);color:var(--white);font-weight:700;font-size:15px;display:flex;align-items:center;justify-content:center}
.arrow{top:414px;width:30px;height:36px;background:#2d3331;display:flex;align-items:center;justify-content:center}
.hero-dots{left:567px;top:630px;display:flex;gap:5px}
.hero-dots span{width:8px;height:8px;border-radius:50%;background:var(--white)}
.hero-dots span.on{background:transparent;border:2px solid var(--white)}
.seal{left:575px;top:712px;width:50px;height:50px;border-radius:50%;background:var(--ink);border:4px solid #f3f0e6}

/* sections */
.section-title{left:0;width:1200px;text-align:center;font-family:"Cinzel",serif;font-weight:600;font-size:54px;color:var(--ink)}
.card{background:var(--white);border:1px solid var(--card-border)}
.photo{width:100%}
.product-name{font-weight:700;font-size:16px;letter-spacing:.3px;margin:20px 0 0 30px}
.price{font-size:14px;color:var(--muted);margin:16px 0 0 30px}
.desc{font-size:12.5px;color:var(--muted);margin:10px 12px 0 30px;line-height:1.55}
.story-title{font-weight:700;font-size:16px;margin:34px 0 0 35px}
.story-text{font-size:12.5px;color:var(--muted);margin:14px 24px 0 35px;line-height:1.7}
.read-more{font-weight:700;font-size:15px;color:var(--slate);margin:14px 0 0 35px}
.dots{left:543px;display:flex;gap:14px}
.dots span{width:12px;height:12px;border-radius:50%;border:1px solid var(--muted)}
.dots span.on{background:var(--muted)}
.footer-seal{left:540px;top:2735px;width:120px;height:120px;border-radius:50%;background:var(--footer)}

/* footer */
.footer{left:0;top:2856px;width:1200px;height:327px;background:var(--footer);color:var(--white)}
.footer-brand{left:155px;top:98px;font-size:24px;color:var(--white)}
.cards{left:183px;top:164px;display:flex;gap:8px}
.cards span{width:32px;height:20px;background:#e8ecea;border-radius:2px}
.col{top:78px}
.col h4{font-size:15px;font-weight:700;margin-bottom:16px;letter-spacing:.3px}
.col li{list-style:none;font-size:11.5px;line-height:24px}
.social li{display:flex;align-items:center;gap:10px}
.social i{width:12px;height:12px;background:var(--white);border-radius:2px}
.copyright{left:0;width:1200px;top:272px;text-align:center;font-size:11.5px}
</style>
</head>
<body>
<div class="page">

  <header>
    <div class="abs search">Search
      <svg width="12" height="12" viewBox="0 0 12 12"><circle cx="5" cy="5" r="3.6" fill="none" stroke="#333" stroke-width="1.6"/><line x1="7.6" y1="7.6" x2="11" y2="11" stroke="#333" stroke-width="1.8"/></svg>
    </div>
    <div class="abs brand header-brand">Willow Lane</div>
    <div class="abs account">Sign in or Register</div>
    <div class="abs cart"><svg width="15" height="13" viewBox="0 0 15 13"><path d="M0 1h3l2 7h8l2-6H4" fill="none" stroke="#1b1f1e" stroke-width="1.6"/><circle cx="6" cy="11" r="1.4" fill="#1b1f1e"/><circle cx="12" cy="11" r="1.4" fill="#1b1f1e"/></svg>Cart 0</div>
    <div class="abs header-rule"></div>
    <nav class="abs nav"><span>HOME</span><span>SALE</span><span>NEW ARRIVALS</span><span>ANTIQUE CROWNS</span><span>ABOUT</span><span>PRODUCTS</span><span>ACCESSORY</span></nav>
  </header>

  <section class="abs hero" role="img" aria-label="Black and white photograph of an antique star crown"></section>
  <div class="abs brand hero-title">Willow Lane</div>
  <div class="abs hero-sub">Lorem ipsum dolor sit amet consectetur adipiscing elit</div>
  <div class="abs btn">SHOP ONLINE</div>
  <div class="abs arrow" style="left:0"><svg width="10" height="14"><path d="M8 1L2 7l6 6" fill="none" stroke="#fff" stroke-width="2"/></svg></div>
  <div class="abs arrow" style="left:1170px"><svg width="10" height="14"><path d="M2 1l6 6-6 6" fill="none" stroke="#fff" stroke-width="2"/></svg></div>
  <div class="abs hero-dots"><span></span><span></span><span class="on"></span><span></span><span></span></div>
  <div class="abs seal"></div>

  <h2 class="abs section-title" style="top:810px">New Arrivals</h2>

  <article class="abs card" style="left:146px;top:930px;width:286px;height:414px">
    <div class="photo" style="height:318px;background:linear-gradient(180deg,#a9a39a,#8a6b3c 70%,#5a3a22)" role="img" aria-label="Gilded antique star crown on old books"></div>
    <div class="product-name">PRODUCT NAME</div><div class="price">$66.86</div>
  </article>
  <article class="abs card" style="left:458px;top:930px;width:286px;height:462px">
    <div class="photo" style="height:318px;background:linear-gradient(180deg,#3b2c1c,#8b6a48 55%,#3a3633)" role="img" aria-label="Jewelled antique crown on a dark stand"></div>
    <div class="product-name">PRODUCT NAME</div><div class="price">$66.86</div>
    <div class="desc">Lorem ipsum dolor sit ameonsectetur adipiscing elit, sed do eiusmod</div>
  </article>
  <article class="abs card" style="left:769px;top:930px;width:286px;height:414px">
    <div class="photo" style="height:318px;background:linear-gradient(180deg,#b8b0a2,#6a5332 55%,#3a3530)" role="img" aria-label="Antique crown set with coloured stones"></div>
    <div class="product-name">PRODUCT NAME</div><div class="price">$66.86</div>
  </article>
  <div class="abs dots" style="top:1444px"><span class="on"></span><span></span><span></span><span></span><span></span></div>

  <h2 class="abs section-title" style="top:1540px">Antiques &amp; Unique Finds</h2>

  <article class="abs card" style="left:170px;top:1667px;width:411px;height:452px">
    <div class="photo" style="height:262px;background:linear-gradient(180deg,#d9b48c,#2a2220 55%,#4a4a55)" role="img" aria-label="Fur crown with jewelled band on books"></div>
    <div class="story-title">LOREM IPSUM DOLOR SITONSECTETUR</div>
    <div class="story-text">Lorem ipsum dolor sit amet, consectetur adipiscing elit, sed do eiusmod tempor incididunt ut labore et dolore magna aliqua. Quis ipsum suspendisse ultrices gravida.</div>
    <div class="read-more">READ MORE</div>
  </article>
  <article class="abs card" style="left:618px;top:1667px;width:411px;height:452px">
    <div class="photo" style="height:262px;background:linear-gradient(135deg,#b09a68,#5b4a3a 50%,#2a2624)" role="img" aria-label="Box of vintage ribbons and trims"></div>
    <div class="story-title">LOREM IPSUM DOLOR SITONSECTETUR</div>
    <div class="story-text">Lorem ipsum dolor sit amet, consectetur adipiscing elit, sed do eiusmod tempor incididunt ut labore et dolore magna aliqua. Quis ipsum suspendisse ultrices gravida.</div>
    <div class="read-more">READ MORE</div>
  </article>
  <article class="abs card" style="left:170px;top:2153px;width:411px;height:452px">
    <div class="photo" style="height:262px;background:linear-gradient(180deg,#c9ad8c,#6b6862 60%,#22201f)" role="img" aria-label="Antique iron helmet on a book"></div>
    <div class="story-title">LOREM IPSUM DOLOR SITONSECTETUR</div>
    <div class="story-text">Lorem ipsum dolor sit amet, consectetur adipiscing elit, sed do eiusmod tempor incididunt ut labore et dolore magna aliqua. Quis ipsum suspendisse ultrices gravida.</div>
    <div class="read-more">READ MORE</div>
  </article>
  <article class="abs card" style="left:618px;top:2153px;width:411px;height:452px">
    <div class="photo" style="height:262px;background:radial-gradient(ellipse at 50% 60%,#5e4c30,#22201d 60%,#b9b0a4)" role="img" aria-label="Embroidered gold bullion badge"></div>
    <div class="story-title">LOREM IPSUM DOLOR SITONSECTETUR</div>
    <div class="story-text">Lorem ipsum dolor sit amet, consectetur adipiscing elit, sed do eiusmod tempor incididunt ut labore et dolore magna aliqua. Quis ipsum suspendisse ultrices gravida.</div>
    <div class="read-more">READ MORE</div>
  </article>
  <div class="abs dots" style="top:2671px"><span class="on"></span><span></span><span></span><span></span><span></span></div>
  <div class="abs footer-seal"></div>

  <footer class="abs footer">
    <div class="abs brand footer-brand">Willow Lane</div>
    <div class="abs cards"><span></span><span></span><span></span><span></span><span></span></div>
    <div class="abs col" style="left:492px"><h4>ABOUT</h4><ul><li>About Us</li><li>A Family Business</li><li>Charity and Community</li><li>Press</li><li>Careers</li></ul></div>
    <div class="abs col" style="left:699px"><h4>TERMS &amp; CONDITIONS</h4><ul><li>Terms and Conditions</li><li>Privacy Policy</li><li>GDPR</li></ul></div>
    <div class="abs col social" style="left:967px"><h4>SOCIAL</h4><ul><li><i></i>Photogram</li><li><i></i>Friendbook</li><li><i></i>Pinboard</li><li><i></i>Chirper</li></ul></div>
    <div class="abs copyright">© 2021 Willow Lane.All Rights reserved &nbsp;| &nbsp;Privacy Terms &nbsp;| &nbsp;Careers &nbsp;| &nbsp;Site Map</div>
  </footer>

</div>
</body>
</html>
```